business card

Business card for new business.
Red and black corporate colors.
Card can have an Indsutrial feel to it. Feel free to add Rust, Bolted steel, or graphics as you see fit. We provide highly specialized services to the below mentioned industries.
Keep information out of corners so that if I want I can choose rounded corners.
Information
- front. name - title - phone - email
- Rear
Refining - Rail - Infrastructure - Mining - Energy
Calgary - Edmonton - Fort McMurray - Revelstoke - Vancouver

```html
<!DOCTYPE html>
<html lang="en">
<head>
<meta charset="utf-8">
<title>Ironspan Business Card</title>
<link href="https://fonts.googleapis.com/css2?family=Arimo:wght@400;700&display=swap" rel="stylesheet">
<style>
  :root {
    --stage: #1b1b1d;
    --card: #050505;
    --card-edge: #222;
    --red: #e0262b;
    --grey: #9a9a9a;
    --grey-light: #b5b5b5;
    --icon-glyph: #140404;
  }
  * { margin: 0; padding: 0; box-sizing: border-box; }
  html, body { width: 1200px; height: 800px; overflow: hidden; }
  body {
    background: var(--stage);
    font-family: "Arimo", Arial, sans-serif;
    display: flex;
    flex-direction: column;
    align-items: center;
    justify-content: center;
    gap: 36px;
  }
  .card {
    position: relative;
    width: 620px;
    height: 354px;
    background: var(--card);
    border: 1px solid var(--card-edge);
    box-shadow: 0 14px 30px rgba(0,0,0,.55);
  }
  .brand {
    display: flex;
    align-items: center;
    gap: 14px;
    font-weight: 700;
    color: var(--grey-light);
    letter-spacing: 2px;
  }
  .brand-mark {
    width: 26px; height: 26px;
    background: var(--red);
  }
  .brand-name { font-size: 52px; line-height: 1; }

  /* Rear */
  .card-rear .brand {
    position: absolute;
    top: 108px; left: 0; right: 0;
    justify-content: center;
  }
  .sectors {
    position: absolute;
    left: 0; right: 0; top: 210px;
    text-align: center;
    color: var(--grey);
    font-size: 15px;
    line-height: 22px;
  }
  .sep { color: var(--red); padding: 0 5px; }

  /* Front */
  .card-front .brand {
    position: absolute;
    top: 78px; left: 62px;
  }
  .divider {
    position: absolute;
    left: 48px; right: 48px; top: 222px;
    height: 1px;
    background: var(--red);
  }
  .person {
    position: absolute;
    left: 48px; top: 176px;
  }
  .person-name {
    color: var(--red);
    font-size: 20px;
    font-weight: 400;
    line-height: 22px;
  }
  .person-title {
    color: var(--grey);
    font-size: 17px;
    line-height: 20px;
  }
  .contacts {
    position: absolute;
    left: 48px; top: 236px;
    list-style: none;
    color: var(--grey);
    font-size: 15px;
  }
  .contacts li {
    display: flex;
    align-items: center;
    gap: 10px;
    height: 25px;
  }
  .contact-icon { width: 19px; height: 19px; display: block; }
  .address {
    position: absolute;
    right: 48px; top: 236px;
    text-align: right;
    color: var(--grey);
    font-size: 15px;
    line-height: 20px;
  }
</style>
</head>
<body>

  <section class="card card-rear">
    <div class="brand">
      <span class="brand-mark"></span>
      <span class="brand-name">IRONSPAN</span>
    </div>
    <div class="sectors">
      <p>Forging<span class="sep">|</span>Marine<span class="sep">|</span>Pipelines<span class="sep">|</span>Quarrying<span class="sep">|</span>Power</p>
      <p>Hallbrook<span class="sep">|</span>Westmere<span class="sep">|</span>Port Ashdale<span class="sep">|</span>Cragmoor<span class="sep">|</span>Elmsford</p>
    </div>
  </section>

  <section class="card card-front">
    <div class="brand">
      <span class="brand-mark"></span>
      <span class="brand-name">IRONSPAN</span>
    </div>

    <div class="person">
      <p class="person-name">REID CALLOWAY</p>
      <p class="person-title">Managing Director</p>
    </div>

    <div class="divider"></div>

    <ul class="contacts">
      <li>
        <svg class="contact-icon" viewBox="0 0 20 20" aria-hidden="true">
          <rect width="20" height="20" fill="var(--red)"/>
          <path d="M5 6c0-1 1-2 2-2l1 3-1.2 1c.8 1.8 2.2 3.2 4 4l1-1.2 3 1c0 1-1 2-2 2C8.5 13.8 5 10.5 5 6z" fill="var(--icon-glyph)"/>
        </svg>
        <span>(01) 5550 1827</span>
      </li>
      <li>
        <svg class="contact-icon" viewBox="0 0 20 20" aria-hidden="true">
          <rect width="20" height="20" fill="var(--red)"/>
          <rect x="4" y="6" width="12" height="8" fill="none" stroke="var(--icon-glyph)" stroke-width="1.5"/>
          <path d="M4 6l6 5 6-5" fill="none" stroke="var(--icon-glyph)" stroke-width="1.5"/>
        </svg>
        <span>info@ironspanworks.com</span>
      </li>
      <li>
        <svg class="contact-icon" viewBox="0 0 20 20" aria-hidden="true">
          <rect width="20" height="20" fill="var(--red)"/>
          <g fill="none" stroke="var(--icon-glyph)" stroke-width="1.3">
            <circle cx="10" cy="10" r="6"/>
            <ellipse cx="10" cy="10" rx="2.6" ry="6"/>
            <path d="M4 10h12M5 7h10M5 13h10"/>
          </g>
        </svg>
        <span>www.ironspanworks.com</span>
      </li>
    </ul>

    <div class="address">
      <p>PO BOX 418 Harbour Lane</p>
      <p>Millgate Leeds, UK</p>
    </div>
  </section>

</body>
</html>
```